Business Card Design Project

Business Card
We are rebranding with a new logo
Industry/Entity Type
Business
Contact Information for Business Card
Dennis Morvale +61 487215963 dennis@quorv.com.au P.O. Box 872 Fernlow QLD 4309
Requirements
Must have
- Logo

```html
<!DOCTYPE html>
<html lang="en">
<head>
<meta charset="utf-8">
<title>Quorv International – Business Card</title>
<link href="https://fonts.googleapis.com/css2?family=Roboto:wght@400;500&family=Roboto+Condensed:wght@700&display=swap" rel="stylesheet">
<style>
  :root {
    --backdrop: #8c8c8c;
    --card-dark: #1b1c1e;
    --card-blue: #0ea3dc;
    --card-blue-deep: #045a80;
    --text-light: #ffffff;
    --accent-orange: #f28a1e;
  }
  * { margin: 0; padding: 0; box-sizing: border-box; }
  html, body {
    width: 1200px; height: 960px; overflow: hidden;
    background: var(--backdrop);
  }
  .business-card {
    position: absolute; left: 315px; top: 295px;
    width: 598px; height: 342px;
    border-radius: 16px; overflow: hidden;
    box-shadow: 0 4px 10px rgba(0,0,0,0.35);
  }
  .card-art { position: absolute; inset: 0; }
  .brand-name {
    position: absolute; left: 40px; top: 128px;
    font-family: "Roboto", sans-serif; font-weight: 500;
    color: var(--accent-orange); line-height: 1;
  }
  .brand-name .brand-main { display: block; font-size: 56px; letter-spacing: 1px; }
  .brand-name .brand-sub { display: block; font-size: 20px; letter-spacing: 3px; margin-top: 14px; }
  .holder-name {
    position: absolute; right: 27px; top: 28px;
    font-family: "Roboto Condensed", sans-serif; font-weight: 700;
    font-size: 20px; color: var(--text-light);
  }
  .postal-address, .contact-list {
    position: absolute; right: 27px;
    font-family: "Roboto", sans-serif; font-size: 13.5px;
    color: var(--text-light); text-align: right; line-height: 18px;
  }
  .postal-address { top: 213px; }
  .contact-list { top: 257px; list-style: none; line-height: 19.5px; }
  .contact-list li { display: flex; justify-content: flex-end; align-items: center; gap: 9px; }
  .contact-icon { width: 12px; height: 12px; fill: var(--text-light); }
</style>
</head>
<body>
  <div class="business-card">
    <svg class="card-art" viewBox="0 0 598 342" aria-hidden="true">
      <defs>
        <radialGradient id="blueGlow" cx="0.62" cy="0.35" r="0.75">
          <stop offset="0" stop-color="#12afe8"/>
          <stop offset="0.55" stop-color="#0a86b8"/>
          <stop offset="1" stop-color="#045a80"/>
        </radialGradient>
      </defs>
      <rect class="blue-field" width="598" height="342" fill="url(#blueGlow)"/>
      <path class="swoosh swoosh-outer" d="M120 0 L290 0 C360 10 400 40 395 95 C385 170 300 260 262 342 L240 342 Z" fill="#0b6f99" opacity="0.7"/>
      <path class="swoosh swoosh-mid" d="M120 0 L250 0 C330 12 370 45 365 100 C355 170 290 260 252 342 L240 342 Z" fill="#08597c" opacity="0.8"/>
      <path class="swoosh swoosh-inner" d="M120 0 L210 0 C300 15 345 50 340 105 C330 175 280 260 246 342 L240 342 Z" fill="#064766"/>
      <path class="dark-field" d="M0 0 L125 0 C270 20 330 60 320 115 C305 185 265 265 243 342 L0 342 Z" fill="var(--card-dark)"/>
    </svg>

    <div class="brand-name">
      <span class="brand-main">Quorv</span>
      <span class="brand-sub">INTERNATIONAL</span>
    </div>

    <div class="holder-name">DENNIS MORVALE</div>

    <address class="postal-address" style="font-style:normal">
      P.O. Box 872<br>Fernlow QLD 4309
    </address>

    <ul class="contact-list">
      <li>+61 487215963
        <svg class="contact-icon" viewBox="0 0 24 24"><path d="M6.6 10.8a15 15 0 0 0 6.6 6.6l2.2-2.2a1 1 0 0 1 1-.25 11.4 11.4 0 0 0 3.6.57 1 1 0 0 1 1 1V20a1 1 0 0 1-1 1A17 17 0 0 1 3 4a1 1 0 0 1 1-1h3.5a1 1 0 0 1 1 1c0 1.25.2 2.45.57 3.57a1 1 0 0 1-.25 1z"/></svg>
      </li>
      <li>dennis@quorv.com.au
        <svg class="contact-icon" viewBox="0 0 24 24"><path d="M2 5h20v14H2z M2 5l10 8 10-8" fill="none" stroke="#fff" stroke-width="0"/><path d="M2 6.5 12 13l10-6.5V19H2z"/><path d="M2 5h20l-10 6.5z"/></svg>
      </li>
      <li>www.quorv.com.au
        <svg class="contact-icon" viewBox="0 0 24 24"><circle cx="12" cy="12" r="11"/><path d="M7 6c2 1 3 3 2 5s1 3 2 4-1 4-1 5M15 4c0 2 2 3 3 3s2 3 0 5-3 3-2 6" fill="none" stroke="#0a7aa8" stroke-width="2"/></svg>
      </li>
    </ul>
  </div>
</body>
</html>
```